Binder design for a veterinary clinic

We are seeking a talented designer to create a standout design for ring binders specifically for our veterinary clinic. These binders will be used to organize materials from our Continuing Professional Development (CPD) projects for colleagues and interns. The design should be clean, professional, and align with our brand guidelines. To give you a better understanding of our branding, we’ve included the design of our vehicles as a reference. As additional reference, please visit www.tierpraxora.at

Target Market(s)

veterinarians

Industry/Entity Type

Veterinary

Font styles to use
Sans Serif

Colors
0054AA
0677BA
7BADD7
CADEEF
E8F1F8
FFC000
F8CF3A
FAE287
FDF2CF
FEFAEE

Requirements
Must have
• Our Logo an a clean design
Should not have
• to much images

```html
<!DOCTYPE html>
<html lang="de">
<head>
<meta charset="utf-8">
<title>Tierpraxora – Ordner</title>
<link href="https://fonts.googleapis.com/css2?family=Montserrat:wght@500;600;700;800&display=swap" rel="stylesheet">
<style>
  :root {
    --bg: #e4e4e4;
    --paper: #f6f6f5;
    --navy: #2f4459;
    --gold: #c99a22;
    --edge: #d9d9d6;
  }
  * { margin: 0; padding: 0; box-sizing: border-box; }
  html, body { width: 1200px; height: 900px; overflow: hidden; }
  body {
    background: var(--bg);
    font-family: "Montserrat", Arial, sans-serif;
    position: relative;
  }
  .binder {
    position: absolute;
    left: 210px; top: 60px;
    display: flex;
    gap: 14px;
  }
  .spine {
    width: 190px; height: 780px;
    background: var(--paper);
    border: 1px solid var(--edge);
    position: relative;
    display: flex;
    flex-direction: column;
    align-items: center;
    padding-top: 90px;
  }
  .spine-mark {
    width: 96px; height: 96px;
    border-radius: 50%;
    border: 4px solid var(--gold);
    background: var(--navy);
    flex: none;
  }
  .spine-label {
    margin-top: 40px;
    writing-mode: vertical-rl;
    white-space: nowrap;
    display: flex;
    gap: 4px;
  }
  .spine-name {
    font-size: 34px; font-weight: 700;
    color: var(--navy);
    letter-spacing: -0.5px;
    line-height: 1.1;
  }
  .spine-tagline {
    font-size: 17px; font-weight: 600;
    color: var(--gold);
    line-height: 1.2;
    padding-top: 4px;
  }
  .cover {
    width: 580px; height: 780px;
    background: var(--paper);
    border: 1px solid var(--edge);
    position: relative;
    overflow: hidden;
  }
  .cover-head {
    position: absolute;
    top: 70px; left: 0; right: 0;
    text-align: center;
  }
  .cover-name {
    font-size: 62px; font-weight: 800;
    color: var(--navy);
    letter-spacing: -1.5px;
    line-height: 1;
  }
  .cover-tagline {
    margin-top: 8px;
    font-size: 26px; font-weight: 700;
    color: var(--gold);
  }
  .cover-ring {
    position: absolute;
    left: 0; top: 0;
    width: 580px; height: 780px;
  }
  .cover-art {
    position: absolute;
    left: 170px; top: 350px;
    width: 520px; height: 520px;
    border-radius: 50%;
    background: linear-gradient(160deg, var(--navy) 0%, var(--navy) 62%, var(--gold) 100%);
  }
</style>
</head>
<body>
  <div class="binder">
    <div class="spine">
      <div class="spine-mark"></div>
      <div class="spine-label">
        <div class="spine-name">Tierpraxora</div>
        <div class="spine-tagline">Fachklinik für Kleintiere</div>
      </div>
    </div>
    <div class="cover">
      <header class="cover-head">
        <div class="cover-name">Tierpraxora</div>
        <div class="cover-tagline">Fachklinik für Kleintiere</div>
      </header>
      <svg class="cover-ring" viewBox="0 0 580 780" aria-hidden="true">
        <circle cx="430" cy="610" r="300" fill="none" stroke="#c99a22" stroke-width="9"/>
      </svg>
      <div class="cover-art" role="img" aria-label="Large illustration of a dog and a cat in silhouette"></div>
    </div>
  </div>
</body>
</html>
```